TEBSIRK HOA Portal Site for Public

Clean up and organize current website; need website to look good and functional; this is a HOA (homeowner association management) website where homeowners can login and pay their bill, general information about a HOA, monthly newsletter page.
Competitors:
https://quillmarsh.example/
https://dorvinpalms.example/
https://www.kelbrookhomes.example/nevada
http://www.tpw-hoa.example/

Target Market(s)

homeowners

Industry/Entity Type

Real Estate

Coding

Coded - Design and coding required

Number of Pages Required

5+ page

Font styles to use
Serif

Colors
0292cd
33a6d7
e667a6
e34297

Requirements
Must have
• login to pay
• services page
• contact us
• order resale package
Nice to have
• page why an HOA would contract us

```html
<!DOCTYPE html>
<html lang="en">
<head>
<meta charset="utf-8">
<title>Tebsirk Association Management</title>
<link href="https://fonts.googleapis.com/css2?family=PT+Serif:ital,wght@0,400;0,700;1,400&family=Roboto+Slab:wght@400;500;700&display=swap" rel="stylesheet">
<style>
:root{
  --blue:#0292cd;
  --blue-light:#33a6d7;
  --blue-deep:#027aab;
  --pink:#e34297;
  --pink-light:#e667a6;
  --black:#0b0b0b;
  --ink:#111;
  --text:#555;
  --white:#fff;
  --card-line:#e2e2e2;
}
*{margin:0;padding:0;box-sizing:border-box}
html,body{width:1200px;height:3209px;overflow:hidden}
body{position:relative;background:var(--white);font-family:"PT Serif",serif;color:var(--ink)}
.abs{position:absolute}
.heading{font-family:"Roboto Slab",serif;font-weight:700;text-transform:uppercase;letter-spacing:.5px}
.btn{position:absolute;background:var(--blue);color:var(--white);font-family:"Roboto Slab",serif;font-weight:700;font-size:14px;text-transform:uppercase;display:flex;align-items:center;justify-content:center;gap:8px;white-space:nowrap}
.btn .dot{width:12px;height:12px;border-radius:50%;background:var(--white)}

/* header */
.topbar{left:0;top:0;width:1200px;height:67px;background:var(--black)}
.nav{left:111px;top:25px;display:flex;gap:16px;font-family:"Roboto Slab",serif;font-size:13px;font-weight:700;color:var(--white);white-space:nowrap}
.nav .active{position:relative}
.nav .active::after{content:"";position:absolute;left:0;right:0;bottom:-16px;height:4px;background:var(--pink)}
.social-top{left:778px;top:27px;display:flex;gap:15px}
.social-top span{width:13px;height:13px;border-radius:50%;background:var(--white)}
.login{left:939px;top:14px;width:149px;height:39px}
.brand-box{left:545px;top:0;width:179px;height:153px;z-index:3}
.brand-name{left:545px;top:52px;width:179px;text-align:center;font-family:"Roboto Slab",serif;font-size:11px;font-weight:700;color:var(--ink);z-index:4;line-height:15px}
.brand-mark{left:621px;top:16px;width:26px;height:26px;background:var(--blue);z-index:4}

/* hero */
.hero{left:0;top:67px;width:1200px;height:548px;background:linear-gradient(100deg,#4a2c22 0%,#6e4130 35%,#8a6a55 55%,#3f3a2c 80%,#23261b 100%)}
.hero-title{left:111px;top:264px;font-size:44px;line-height:53px;color:var(--white)}
.hero-btn{left:112px;top:402px;width:169px;height:40px}
.badge{left:533px;top:560px;width:110px;height:110px;border-radius:50%;background:var(--white)}
.badge::after{content:"";position:absolute;left:35px;top:35px;width:40px;height:40px;border-radius:50%;background:var(--blue)}

/* about */
.about-photo{left:111px;top:752px;width:468px;height:394px;background:linear-gradient(160deg,#b9c7cf,#5e6a73 50%,#7a4a40);border:3px solid var(--white);box-shadow:0 0 6px rgba(0,0,0,.25)}
.play{left:310px;top:915px;width:70px;height:70px;border:3px solid var(--white);border-radius:50%}
.play::after{content:"";position:absolute;left:25px;top:17px;border-left:24px solid var(--white);border-top:15px solid transparent;border-bottom:15px solid transparent}
.about-title{left:665px;top:806px;font-size:42px}
.about-text{left:665px;top:884px;width:390px;font-size:15px;line-height:26px;color:var(--text);text-align:justify}
.read-more{left:665px;top:1043px;width:168px;height:40px}

/* partners */
.partners{left:0;top:1232px;width:1200px;height:296px;background:linear-gradient(90deg,#151515,#0a0a0a 50%,#141414)}
.partners-title{left:0;top:1314px;width:1200px;text-align:center;font-size:42px;color:var(--white)}
.partner-card{top:1466px;width:232px;height:154px;background:var(--white);border:1px solid var(--card-line);box-shadow:0 1px 4px rgba(0,0,0,.15);display:flex;align-items:center;justify-content:center;gap:10px;font-family:"Roboto Slab",serif;font-size:17px;font-weight:700;color:#333;text-align:center;line-height:22px}
.partner-card i{width:16px;height:16px;background:#333;display:block;flex:none}

/* articles */
.articles-title{left:0;top:1718px;width:1200px;text-align:center;font-size:42px}
.article-photo{top:1845px;width:455px;height:286px;border:3px solid var(--white);box-shadow:0 0 6px rgba(0,0,0,.25)}
.article-box{top:2082px;width:384px;height:208px;background:var(--white);border-left:9px solid var(--pink);border-bottom:9px solid var(--pink);box-shadow:2px 2px 6px rgba(0,0,0,.12);text-align:center;padding-top:20px}
.article-box h3{font-family:"Roboto Slab",serif;font-size:20px;font-weight:500;text-transform:uppercase;margin-bottom:14px}
.article-box p{font-size:15px;line-height:26px;color:var(--text);white-space:nowrap}
.article-box .date{margin-top:12px;font-family:"Roboto Slab",serif;font-size:16px;font-weight:500;display:flex;justify-content:center;align-items:center;gap:12px}
.article-box .date i{width:14px;height:14px;background:var(--blue);display:block}

/* testimonial */
.testimonial{left:0;top:2389px;width:1200px;height:406px;background:linear-gradient(90deg,#121212,#1b1b17 50%,#101010)}
.quote-box{left:111px;top:2356px;width:90px;height:84px;background:var(--pink);border:4px solid var(--white)}
.quote-box svg{position:absolute;left:19px;top:17px}
.testi-title{left:0;top:2452px;width:1200px;text-align:center;font-size:42px;color:var(--white)}
.testi-text{left:0;top:2540px;width:1200px;text-align:center;font-size:15px;line-height:26px;font-style:italic;color:var(--white);white-space:nowrap}
.testi-author{left:0;top:2642px;width:1200px;text-align:center;font-size:15px;color:var(--white)}
.dots{left:572px;top:2709px;display:flex;gap:8px}
.dots span{width:13px;height:13px;border-radius:50%;background:var(--pink)}
.dots .on{background:var(--white)}

/* footer */
.footer{left:0;top:2795px;width:1200px;height:365px;background:var(--blue)}
.foot-col{top:2874px;color:var(--white)}
.foot-col h4{font-family:"Roboto Slab",serif;font-size:20px;font-weight:700;text-decoration:underline;text-transform:uppercase;margin-bottom:8px}
.foot-col li{list-style:none;font-size:17px;line-height:34px;display:flex;align-items:center;gap:11px;white-space:nowrap}
.foot-col li::before{content:"»";font-size:17px}
.foot-col.social li::before{content:"";width:12px;height:12px;background:var(--white)}
.field{left:812px;width:278px;border:1px solid #d9eff8;background:rgba(255,255,255,.14);color:var(--white);font-size:16px;padding:5px 0 0 44px}
.field::before{content:"";position:absolute;left:14px;top:9px;width:14px;height:12px;border:2px solid var(--white);border-radius:2px}
.subscribe{left:812px;top:3086px;width:146px;height:41px;background:var(--white);color:var(--blue);font-family:"Roboto Slab",serif;font-size:16px;font-weight:700;display:flex;align-items:center;justify-content:center}
.copyright{left:0;top:3160px;width:1200px;height:49px;background:var(--blue-deep);color:var(--white);font-size:17px;text-align:center;line-height:49px}
</style>
</head>
<body>

<header>
  <div class="abs topbar"></div>
  <nav class="abs nav"><span class="active">HOME</span><span>ABOUT</span><span>SERVICES</span><span>PARTNER WITH US</span><span>CONTACT US</span></nav>
  <svg class="abs brand-box" viewBox="0 0 179 153"><polygon points="0,0 179,0 179,125 89.5,153 0,125" fill="#fff"/></svg>
  <div class="abs brand-mark"></div>
  <div class="abs brand-name">TEBSIRK ASSOCIATION<br>MANAGEMENT</div>
  <div class="abs social-top"><span></span><span></span><span></span><span></span></div>
  <div class="btn login">Login to pay</div>
</header>

<section>
  <div class="abs hero" role="img" aria-label="Smiling family standing in front of a brick house"></div>
  <h1 class="abs heading hero-title">Tebsirk Association<br>Management</h1>
  <div class="btn hero-btn">Get more info <span class="dot"></span></div>
  <div class="abs badge"></div>
</section>

<section>
  <div class="abs about-photo" role="img" aria-label="Family of three generations outdoors in front of modern homes"></div>
  <div class="abs play"></div>
  <h2 class="abs heading about-title">About Us</h2>
  <p class="abs about-text">We also have special expertise working with complex communities that have large budgets and offer numerous amenities to their residents. In addition, we manage commercial associations and mixed-use developments, as well as multi-family and investor-owned .</p>
  <div class="btn read-more">Read more <span class="dot"></span></div>
</section>

<section>
  <div class="abs partners" role="img" aria-label="Dark photo backdrop of a family"></div>
  <h2 class="abs heading partners-title">Partner With Us</h2>
  <div class="abs partner-card" style="left:114px"><i></i>HALVANE<br>CONSTRUCTION</div>
  <div class="abs partner-card" style="left:362px"><i></i>KESTRO<br>CONSTRUCTION</div>
  <div class="abs partner-card" style="left:608px"><i></i>ORLEND<br>DECK &amp; BUILD</div>
  <div class="abs partner-card" style="left:856px"><i></i>BRENMOOR<br>CONSTRUCTION</div>
</section>

<section>
  <h2 class="abs heading articles-title">Articles</h2>
  <div class="abs article-photo" style="left:111px;background:linear-gradient(135deg,#c8a27a,#8e9aa6 55%,#4e6f96)" role="img" aria-label="Older woman at home looking at her phone in a kitchen"></div>
  <div class="abs article-photo" style="left:633px;background:linear-gradient(135deg,#a7b8c9,#7f8fa4 50%,#4d7db5)" role="img" aria-label="Group of seniors laughing together on a sofa"></div>
  <div class="abs article-box" style="left:152px">
    <h3>Aging Gracefully</h3>
    <p>Florida's population of residents<br>65 years old and over is the largest in the<br>nation and growing.</p>
    <div class="date"><i></i>05 &nbsp;AUGUST 2019</div>
  </div>
  <div class="abs article-box" style="left:674px">
    <h3>Elderly New Yorkers</h3>
    <p>While many older New Yorkers head<br>west for their sunset years, a growing number<br>of city residents are staying right.</p>
    <div class="date"><i></i>06 &nbsp;AUGUST 2019</div>
  </div>
</section>

<section>
  <div class="abs testimonial" role="img" aria-label="Dark photo backdrop of a house at dusk"></div>
  <div class="abs quote-box">
    <svg width="44" height="42" viewBox="0 0 44 42"><path d="M2 20 Q2 4 18 2 V9 Q10 10 10 18 H18 V40 H2 Z M26 20 Q26 4 42 2 V9 Q34 10 34 18 H42 V40 H26 Z" fill="#fff"/></svg>
  </div>
  <h2 class="abs heading testi-title">Testimonial</h2>
  <p class="abs testi-text">“ &nbsp;There are many variations of passages of Lorem Ipsum available, but the majority have suffered<br>alteration in some form, by injected humour, or randomised words which don't look even slightly believable.<br>If you are going to use a passage of Lorem Ipsum, you need to be sure &nbsp;”</p>
  <p class="abs testi-author"><b>D.L. Marsh,</b> Businessman</p>
  <div class="abs dots"><span></span><span class="on"></span><span></span></div>
</section>

<footer>
  <div class="abs footer"></div>
  <div class="abs foot-col" style="left:124px"><h4>Quick Links</h4><ul><li>Home</li><li>About Us</li><li>Services</li><li>Partner With Us</li><li>Contact Us</li></ul></div>
  <div class="abs foot-col" style="left:325px"><h4>Other Links</h4><ul><li>Order Resale Package</li><li>Terms &amp; Conditions</li><li>Privacy Policy</li><li>FAQ</li><li>Newsletter</li></ul></div>
  <div class="abs foot-col social" style="left:592px"><h4>Find Us On</h4><ul><li>Pagebook</li><li>Chirper</li><li>pinboard</li><li>Snapgram</li></ul></div>
  <div class="abs foot-col" style="left:812px"><h4>Subscribe</h4></div>
  <div class="abs field" style="top:2929px;height:31px">Email</div>
  <div class="abs field" style="top:2972px;height:31px">Name</div>
  <div class="abs field" style="top:3015px;height:58px">Message</div>
  <div class="abs subscribe">SUBSCRIBE</div>
  <div class="abs copyright">Copyrights @ 2019 Tebsirk Association Management. All Rights Reserved</div>
</footer>

</body>
</html>
```